Northvale Strategy Partners Website Design

I need a website design for my new business consulting and executive coaching firm, Northvale Strategy Partners. We provide consultative services to business C-suites as well as personal coaching to executives. I have attached the logo with color scheme I have chosen. I would like the website to reflect professionalism and continue the color scheme in the logo.

Target Market(s)

Small to medium business and their executives; middle to upper income men and women in mid- to late career looking for significance

Industry/Entity Type

Business Consultant

Number of Pages Required

4 page

Requirements
Must have
• A homepage with prominent logo and way to contact for more information; an area on the homepage with easy to read, clear text to describe what the company does; a prominent area on the homepage for a tagline; a blog page that can be updated regularly, an "about us" page with biographical information; an "about us" page; a page detailing services offered
• The web design must match the logo colors and font that I have uploaded.
Nice to have
• A lighthouse picture in the background or header
Should not have
• A lot of text area on the homepage

```html
<!DOCTYPE html>
<html lang="en">
<head>
<meta charset="utf-8">
<title>Northvale Strategy Partners</title>
<link rel="stylesheet" href="https://fonts.googleapis.com/css2?family=Montserrat:wght@400;500;600&family=Open+Sans:wght@300;400;600;700&family=Roboto:wght@400;500&display=swap">
<style>
:root{
  --navy:#1e2b5c;
  --navy-text:#2a3a6e;
  --ink:#2b2b2b;
  --body:#3c3c3c;
  --muted:#8a8a8a;
  --white:#ffffff;
  --rule:#6e7690;
  --band-dark:#2a2130;
}
*{margin:0;padding:0;box-sizing:border-box}
html,body{width:1200px;height:2314px;overflow:hidden;background:var(--white)}
body{position:relative;font-family:"Open Sans",sans-serif;color:var(--body)}
.abs{position:absolute}

/* hero */
.hero{position:absolute;left:0;top:0;width:1200px;height:656px;
  background:linear-gradient(90deg,#d9dde3 0%,#eef0f3 30%,#f5f6f7 55%,#d7dbe1 80%,#9aa2ad 100%)}
.brand{position:absolute;left:80px;top:92px;display:flex;align-items:center;gap:12px}
.brand-mark{width:22px;height:22px;background:var(--navy)}
.brand-name{font-family:"Open Sans",sans-serif;font-weight:600;font-size:20px;color:var(--navy);letter-spacing:.3px}
.main-nav{position:absolute;top:60px;left:634px;height:46px;display:flex;align-items:center;
  font-family:"Roboto",sans-serif;font-size:17px;color:#111}
.main-nav a{color:inherit;text-decoration:none;position:absolute;white-space:nowrap;top:12px}
.main-nav .active{left:0;top:0;width:103px;height:46px;border-radius:23px;background:var(--navy);color:var(--white);
  display:flex;align-items:center;justify-content:center}
.slider-dots{position:absolute;top:605px;left:560px;width:90px;height:20px}
.dot{position:absolute;width:7px;height:7px;border-radius:50%;background:#111;top:6px}
.dot-ring{position:absolute;width:19px;height:19px;border-radius:50%;border:2px solid #111;top:0;left:2px}
.dot-ring::after{content:"";position:absolute;left:4px;top:4px;width:7px;height:7px;border-radius:50%;background:#111}

/* section titles */
.section-title{position:absolute;left:0;width:1200px;text-align:center;font-family:"Open Sans",sans-serif;
  font-weight:300;font-size:36px;color:var(--navy-text);text-transform:uppercase;letter-spacing:.2px}
.title-rule{position:absolute;left:517px;width:168px;height:1px;background:var(--rule)}
.intro{position:absolute;left:170px;top:797px;width:860px;text-align:center;font-size:16.5px;line-height:29.5px;color:var(--ink)}

/* features */
.feature{position:absolute;top:932px;width:300px;text-align:center}
.feature-icon{width:114px;height:114px;margin:0 auto;border-radius:50%;border:1.5px solid #b9b9b9;background:#f0f0f0;
  display:flex;align-items:center;justify-content:center}
.feature-icon.current{border-color:var(--navy);background:var(--white)}
.feature-title{margin-top:28px;font-family:"Montserrat",sans-serif;font-weight:500;font-size:20.5px;color:#1a1a1a}
.feature-title.current{color:var(--navy-text)}
.feature-text{margin-top:8px;font-size:14.5px;line-height:24px;color:var(--body)}

/* subscribe band */
.subscribe{position:absolute;left:0;top:1198px;width:1200px;height:406px;
  background:linear-gradient(180deg,#2c2233 0%,#3a2a3a 55%,#2c2430 75%,#1f1c24 100%)}
.subscribe-title{position:absolute;top:82px;left:0;width:1200px;text-align:center;font-weight:300;font-size:36px;color:var(--white)}
.subscribe-sub{position:absolute;top:134px;left:0;width:1200px;text-align:center;font-size:18px;color:var(--white)}
.email-field{position:absolute;left:319px;top:218px;width:562px;height:46px;border:1.5px solid #d8d8d8;
  font-size:18px;color:var(--white);padding:10px 18px}
.subscribe-btn{position:absolute;left:319px;top:275px;width:562px;height:46px;background:var(--white);
  font-weight:700;font-size:18px;color:var(--navy);text-align:center;line-height:46px;letter-spacing:.5px}

/* testimonials */
.avatar{position:absolute;left:555px;top:1743px;width:86px;height:86px;border-radius:50%;
  background:linear-gradient(180deg,#c9ccd1,#8e8c8e)}
.quote{position:absolute;left:190px;top:1853px;width:820px;text-align:center;font-size:16.5px;line-height:25px;color:var(--ink)}
.quote-mark{position:absolute;font-family:"Open Sans",sans-serif;font-weight:700;font-size:34px;color:#333;line-height:1}
.quote-name{position:absolute;top:1921px;left:0;width:1200px;text-align:center;font-weight:700;font-size:17.5px;color:var(--navy-text)}
.t-dots{position:absolute;top:1981px;left:519px;height:14px}
.t-dot{position:absolute;top:0;width:12px;height:12px;border-radius:50%;background:#111}
.t-dot.open{background:var(--white);border:1.5px solid #111}

/* footer */
.site-footer{position:absolute;left:0;top:2053px;width:1200px;height:261px;background:var(--navy);color:var(--white)}
.footer-nav{position:absolute;left:77px;top:39px;font-family:"Roboto",sans-serif;font-size:14.5px}
.footer-nav a{position:absolute;color:var(--white);text-decoration:none;white-space:nowrap;top:17px}
.footer-nav .active{left:0;top:0;width:103px;height:51px;border:1.5px solid var(--white);border-radius:26px;
  display:flex;align-items:center;justify-content:center}
.social{position:absolute;top:47px;width:36px;height:36px;border-radius:50%}
.social.solid{background:var(--white)}
.social.line{border:1.5px solid rgba(255,255,255,.35)}
.footer-rule{position:absolute;left:77px;top:128px;width:1046px;height:1px;background:rgba(255,255,255,.3)}
.contact-icon{position:absolute;top:166px;width:57px;height:57px;border-radius:50%;background:var(--white);
  display:flex;align-items:center;justify-content:center}
.contact-label{position:absolute;top:172px;font-family:"Montserrat",sans-serif;font-size:10.5px;color:#c9cde0}
.contact-value{position:absolute;top:186px;font-family:"Montserrat",sans-serif;font-weight:500;font-size:16px;color:var(--white)}
.copyright{position:absolute;right:77px;top:186px;font-size:11.5px;color:var(--white)}
.copyright span{color:#8f9fd6}
</style>
</head>
<body>

<header class="hero" role="img" aria-label="Photo of a consultant presenting at a flip chart to a seated business team in a bright office">
  <div class="brand"><span class="brand-mark"></span><span class="brand-name">Northvale Strategy Partners</span></div>
  <nav class="main-nav">
    <a class="active" href="#">HOME</a>
    <a href="#" style="left:125px">ABOUT US</a>
    <a href="#" style="left:259px">SERVICES</a>
    <a href="#" style="left:385px">CONTACT US</a>
  </nav>
  <div class="slider-dots">
    <span class="dot-ring"></span>
    <span class="dot" style="left:38px"></span>
    <span class="dot" style="left:69px"></span>
  </div>
</header>

<h2 class="section-title" style="top:708px">Know About Us</h2>
<div class="title-rule" style="top:762px"></div>
<p class="intro">Lorem ipsum dolor sit amet, consectetur adipiscing elit, sed do eiusmod tempor incididunt ut labore et dolore magna aliqua. Ut enim ad minim veniam, quis nostrud exercitation ullamco laboris nisi ut aliquip ex ea commodo consequat. Duis aute irure dolor in reprehenderit.</p>

<div class="feature" style="left:172px">
  <div class="feature-icon">
    <svg width="56" height="50" viewBox="0 0 56 50" fill="#8c8c8c"><circle cx="38" cy="10" r="8"/><path d="M26 32c0-9 5-14 12-14s12 5 12 14z"/><circle cx="16" cy="24" r="7"/><path d="M4 46c0-8 5-12 12-12s12 4 12 12z"/><path d="M6 16a12 12 0 0 1 14-10l-2-3 6 4-5 5 1-3a9 9 0 0 0-11 8z"/></svg>
  </div>
  <div class="feature-title">Consultative Services</div>
  <div class="feature-text">Lorem ipsum dolor sit amet,<br>consectetur adipiscing elit.</div>
</div>
<div class="feature" style="left:450px">
  <div class="feature-icon current">
    <svg width="56" height="44" viewBox="0 0 56 44" fill="#1e2b5c"><circle cx="18" cy="11" r="9"/><circle cx="38" cy="11" r="9"/><path d="M2 42c0-12 7-18 16-18s16 6 16 18z"/><path d="M22 42c0-12 7-18 16-18s16 6 16 18z"/></svg>
  </div>
  <div class="feature-title current">Executive Coaching</div>
  <div class="feature-text">Lorem ipsum dolor sit amet,<br>consectetur adipiscing elit.</div>
</div>
<div class="feature" style="left:725px">
  <div class="feature-icon">
    <svg width="56" height="48" viewBox="0 0 56 48" fill="none" stroke="#8c8c8c" stroke-width="3"><ellipse cx="32" cy="18" rx="20" ry="14"/><path d="M18 28l-10 12 14-7"/><text x="32" y="25" text-anchor="middle" font-family="Open Sans,sans-serif" font-size="18" font-weight="700" fill="#8c8c8c" stroke="none">$</text></svg>
  </div>
  <div class="feature-title">Lorem Ipsume dolor</div>
  <div class="feature-text">Lorem ipsum dolor sit amet,<br>consectetur adipiscing elit.</div>
</div>

<section class="subscribe" role="img" aria-label="Dusk photo of a lighthouse silhouette on the coast under a purple sky">
  <h2 class="subscribe-title">QUICK KEEP IN TOUCH WITH US</h2>
  <p class="subscribe-sub">Subscribe here to Get Connect With Us</p>
  <div class="email-field">Email Id</div>
  <div class="subscribe-btn">SUBSCRIBE</div>
</section>

<h2 class="section-title" style="top:1650px">What People Say</h2>
<div class="title-rule" style="top:1704px"></div>
<div class="avatar" role="img" aria-label="Portrait photo of a smiling client"></div>
<span class="quote-mark" style="left:178px;top:1841px">"</span>
<span class="quote-mark" style="left:1002px;top:1841px">"</span>
<p class="quote">Lorem ipsum dolor sit amet, consectetur adipiscing elit, sed do eiusmod tempor incididunt ut labore et dolore magna aliqua. Ut enim ad minim veniam, quis nostrud.</p>
<div class="quote-name">-NAME HERE</div>
<div class="t-dots">
  <span class="t-dot" style="left:0"></span>
  <span class="t-dot open" style="left:21px"></span>
  <span class="t-dot" style="left:42px"></span>
  <span class="t-dot" style="left:63px"></span>
  <span class="t-dot" style="left:84px"></span>
  <span class="t-dot" style="left:105px"></span>
  <span class="t-dot" style="left:126px"></span>
  <span class="t-dot" style="left:147px"></span>
</div>

<footer class="site-footer">
  <nav class="footer-nav">
    <a class="active" href="#">HOME</a>
    <a href="#" style="left:122px">ABOUT US</a>
    <a href="#" style="left:250px">SERVICES</a>
    <a href="#" style="left:372px">CONTACT US</a>
  </nav>
  <span class="social solid" style="left:963px"></span>
  <span class="social line" style="left:1003px"></span>
  <span class="social line" style="left:1045px"></span>
  <span class="social line" style="left:1086px"></span>
  <div class="footer-rule"></div>

  <div class="contact-icon" style="left:77px">
    <svg width="16" height="24" viewBox="0 0 16 24"><rect x="1" y="1" width="14" height="22" rx="2.5" fill="#1e2b5c"/><rect x="3.5" y="4" width="9" height="13" fill="#fff"/><circle cx="8" cy="20" r="1.3" fill="#fff"/></svg>
  </div>
  <div class="contact-label" style="left:151px">Call Us Today</div>
  <div class="contact-value" style="left:151px">+1 555 014 2880</div>

  <div class="contact-icon" style="left:296px">
    <svg width="24" height="18" viewBox="0 0 24 18"><rect x="0" y="0" width="24" height="18" rx="2" fill="#1e2b5c"/><path d="M1 2l11 8 11-8" fill="none" stroke="#fff" stroke-width="2"/></svg>
  </div>
  <div class="contact-label" style="left:375px">Mail Us Today</div>
  <div class="contact-value" style="left:375px">hello@northvale.example</div>

  <div class="copyright">© <span>NORTHVALE STRATEGY PARTNERS</span> - 2015. All Rights Reserved</div>
</footer>

</body>
</html>
```